Four in One (Flexible infographic for Content Management Industry)

See attachment.
A graphic depicting 4 products, where each can stand on its own and each can be combined with others, but where, if all are taken together, the best result is achieved (the "super product").
Intended use is web. See attached file as an example.
The most basic idea is as the attached diagram shows, where 4 rectangles are arranged in a quadrangle, with a middle rectangle in the center representing the combined 4 products. This concept is fine except it is a bit too obvious as it stands. We are looking for either a variation of this or another concept.
The audience is technical + professional + enterprise - NOT consumers. Hence the design should be conservative in nature.
We are aware of tools like as Canva or Pictogram where such graphics are available, but we are looking for something with a bit more imagination and flexibility.
This graphic should be targeted to web sites and be delivered with vector-based (SVG) graphics.

```html
<!DOCTYPE html>
<html lang="en">
<head>
<meta charset="utf-8">
<title>Four in One – Super Product</title>
<link rel="stylesheet" href="https://fonts.googleapis.com/css2?family=Montserrat:wght@600;700;800&display=swap">
<style>
  :root {
    --page: #ffffff;
    --frame: #9d9d9f;
    --ink: #333336;
    --teal: #3c7482;
    --teal-rule: #2a7a86;
    --teal-tab: #3d7785;
    --navy-tab: #2f3c4b;
    --slate: #53668c;
    --plum: #643355;
    --orchid: #8e4c84;
    --white: #ffffff;
  }
  html, body {
    margin: 0;
    padding: 0;
    width: 1200px;
    height: 982px;
    overflow: hidden;
    background: var(--page);
  }
  .infographic {
    display: block;
    width: 1200px;
    height: 982px;
    font-family: "Montserrat", Arial, sans-serif;
  }
  .outer-frame { fill: none; stroke: var(--frame); stroke-width: 10; stroke-linejoin: miter; }
  .lobe { fill: none; stroke-width: 12; }
  .lobe--documents { stroke: var(--teal); }
  .lobe--security { stroke: var(--teal); }
  .lobe--erp { stroke: var(--slate); }
  .lobe--digital { stroke: var(--plum); }
  .tab--documents { fill: var(--navy-tab); }
  .tab--security { fill: var(--teal-tab); }
  .tab--erp { fill: var(--slate); }
  .tab--digital { fill: var(--orchid); }
  .icon { fill: none; stroke: var(--white); stroke-width: 5; stroke-linejoin: round; stroke-linecap: round; }
  .icon-fill { fill: var(--white); }
  .hub { fill: var(--plum); }
  .hub-title { fill: var(--white); font-weight: 800; font-size: 98px; }
  .card-title { fill: var(--ink); font-weight: 600; font-size: 37px; }
  .card-title--small { font-size: 34px; }
  .rule--teal { stroke: var(--teal-rule); stroke-width: 3; }
  .rule--dark { stroke: var(--ink); stroke-width: 3; }
  .card-text { fill: var(--ink); font-weight: 700; font-size: 19.5px; }
  .feature { fill: var(--ink); font-weight: 600; font-size: 20px; letter-spacing: 0.2px; }
  .tick { fill: none; stroke: var(--ink); stroke-width: 3.2; stroke-linecap: round; stroke-linejoin: round; }
</style>
</head>
<body>
<svg class="infographic" viewBox="0 0 2121 1736" xmlns="http://www.w3.org/2000/svg" role="img" aria-label="Four products combining into one Super Product">
  <defs>
    <path id="tick" class="tick" d="M0,0 L5,5 L14,-5"/>
  </defs>

  <path class="outer-frame" d="M347,153 H735 C900,153 1030,280 1062,400 C1094,280 1224,153 1390,153 H1778 V215 H1835 V443 L1778,476 V560 C1778,700 1680,810 1535,866 C1680,922 1778,1040 1778,1190 V1270 L1835,1305 V1535 H1778 V1583 H1390 C1224,1583 1094,1456 1062,1330 C1030,1456 900,1583 735,1583 H347 V1535 H287 V1305 L347,1270 V1190 C347,1040 445,922 590,866 C445,810 347,700 347,560 V476 L287,443 V215 H347 Z"/>

  <path class="lobe lobe--documents" d="M1027,780 V495 C1027,320 890,195 730,195 H389 V540 C389,690 500,812 655,830"/>
  <path class="lobe lobe--security" d="M1098,780 V495 C1098,320 1235,195 1395,195 H1736 V540 C1736,690 1625,812 1470,830"/>
  <path class="lobe lobe--erp" d="M655,905 C500,925 389,1040 389,1200 V1540 H730 C890,1540 1027,1415 1027,1240 V945"/>
  <path class="lobe lobe--digital" d="M1470,905 C1625,925 1736,1040 1736,1200 V1540 H1395 C1235,1540 1098,1415 1098,1240 V945"/>

  <path class="tab--documents" d="M327,258 H558 A80,80 0 0 1 638,338 V401 H327 Z"/>
  <path class="tab--security" d="M1795,258 H1563 A80,80 0 0 0 1483,338 V401 H1795 Z"/>
  <path class="tab--erp" d="M327,1349 H638 V1412 A80,80 0 0 1 558,1492 H327 Z"/>
  <path class="tab--digital" d="M1795,1349 H1483 V1412 A80,80 0 0 0 1563,1492 H1795 Z"/>

  <g class="icon">
    <path d="M503,280 H553 L570,297 V372 H503 Z"/>
    <path d="M553,280 V297 H570"/>
    <path d="M514,300 H545 M514,313 H558 M514,326 H558 M514,339 H558"/>

    <path d="M1585,280 C1568,290 1556,295 1544,295 V330 C1544,355 1562,372 1585,380 C1608,372 1626,355 1626,330 V295 C1614,295 1602,290 1585,280 Z"/>
    <circle cx="1585" cy="331" r="23"/>
    <path d="M1574,331 L1582,339 L1597,322"/>

    <path d="M508,1390 H578 V1473 H508 Z"/>
    <path d="M492,1374 H562 V1458 H492 Z" fill="var(--slate)"/>
    <path d="M506,1392 H552 M506,1406 H552 M506,1420 H552 M506,1434 H552"/>
  </g>
  <g>
    <path class="icon" d="M1530,1400 A66,66 0 0 1 1622,1400" stroke-width="9"/>
    <path class="icon" d="M1546,1417 A43,43 0 0 1 1606,1417" stroke-width="9"/>
    <path class="icon" d="M1561,1433 A21,21 0 0 1 1591,1433" stroke-width="9"/>
    <circle class="icon-fill" cx="1576" cy="1446" r="12"/>
  </g>

  <rect class="hub" x="645" y="776" width="837" height="172" rx="86"/>
  <text class="hub-title" x="707" y="894" textLength="703" lengthAdjust="spacingAndGlyphs">Super Product</text>

  <!-- Document Management -->
  <text class="card-title" x="469" y="463" textLength="483" lengthAdjust="spacingAndGlyphs">Document Management</text>
  <line class="rule--teal" x1="475" y1="487" x2="960" y2="487"/>
  <text class="card-text" text-anchor="end">
    <tspan x="975" y="532">Streamline document organization, access, and</tspan>
    <tspan x="975" y="556">collaboration with easier file storage and sharing,</tspan>
    <tspan x="975" y="581">leading to more efficient workflows .</tspan>
  </text>
  <use href="#tick" x="539" y="646"/><text class="feature" x="562" y="650">Centralized Document Control</text>
  <use href="#tick" x="539" y="670"/><text class="feature" x="562" y="674">Collaborative Workspace Integration</text>
  <use href="#tick" x="539" y="695"/><text class="feature" x="562" y="699">Automated Compliance Tracking</text>
  <use href="#tick" x="539" y="719"/><text class="feature" x="562" y="723">Check 4</text>

  <!-- Security and Compliance -->
  <text class="card-title" x="1159" y="463" textLength="508" lengthAdjust="spacingAndGlyphs">Security and Compliance</text>
  <line class="rule--teal" x1="1163" y1="487" x2="1667" y2="487"/>
  <text class="card-text">
    <tspan x="1160" y="532">Benefit from tailored cloud solutions, secure data</tspan>
    <tspan x="1160" y="556">storage, and expert disaster recovery planning for</tspan>
    <tspan x="1160" y="580">reliable and scalable IT operations.</tspan>
  </text>
  <use href="#tick" x="1170" y="646"/><text class="feature" x="1207" y="650">Custom Cloud Solutions</text>
  <use href="#tick" x="1170" y="670"/><text class="feature" x="1207" y="674">Secure Data Storage</text>
  <use href="#tick" x="1170" y="695"/><text class="feature" x="1207" y="699">Expert Disaster Recovery</text>
  <use href="#tick" x="1170" y="719"/><text class="feature" x="1207" y="723">Check 4</text>

  <!-- Enterprise Resource Planning -->
  <text class="card-title card-title--small" x="495" y="1052" textLength="483" lengthAdjust="spacingAndGlyphs">Enterprise Resource Planning</text>
  <line class="rule--dark" x1="499" y1="1074" x2="970" y2="1074"/>
  <text class="card-text" text-anchor="end">
    <tspan x="972" y="1117">Simplify management across finance, sales, and</tspan>
    <tspan x="972" y="1141">operations, enabling better decision-making</tspan>
    <tspan x="972" y="1166">and improved productivity.</tspan>
  </text>
  <use href="#tick" x="515" y="1232"/><text class="feature" x="543" y="1236">Integrated Business Processes</text>
  <use href="#tick" x="515" y="1257"/><text class="feature" x="543" y="1261">Enhanced Decision-Making</text>
  <use href="#tick" x="515" y="1281"/><text class="feature" x="543" y="1285">Productivity Improvement</text>
  <use href="#tick" x="515" y="1306"/><text class="feature" x="543" y="1310">Check 4</text>

  <!-- Digital Transformation -->
  <text class="card-title card-title--small" x="1159" y="1052" textLength="401" lengthAdjust="spacingAndGlyphs">Digital Transformation</text>
  <line class="rule--dark" x1="1163" y1="1074" x2="1634" y2="1074"/>
  <text class="card-text">
    <tspan x="1160" y="1119">Turn scanned documents into easily searchable</tspan>
    <tspan x="1160" y="1143">digital archives, boosting efficiency and</tspan>
    <tspan x="1160" y="1168">accessibility.</tspan>
  </text>
  <use href="#tick" x="1170" y="1232"/><text class="feature" x="1207" y="1236">Instant searchable Archives with OCR</text>
  <use href="#tick" x="1170" y="1257"/><text class="feature" x="1207" y="1261">Automated Document Classification</text>
  <use href="#tick" x="1170" y="1281"/><text class="feature" x="1207" y="1285">TeamVault and Cloud Blob Ready</text>
  <use href="#tick" x="1170" y="1306"/><text class="feature" x="1207" y="1310">Check 4</text>
</svg>
</body>
</html>
```